Request for Business Card Design

Hi. My name is Marlene, I am looking for a new business card design for my company, Quarrow Signal Instruments, LLC. I really like the design you did for Tarsel Venture and was hoping you could do something similar using our full logo and our mark. I am also open to any raised texture design using our mark. I have attached our full logo, which would need to be somewhere on the card, as well as the mark in both outline and full form, as well as our brand colors / guide. The card does not have to be white, as long as our logo and mark appear. I actually like darker colored business cards more, but am open to all options. If you are interested in working with me, please let me know. We would also take the business card design into letterhead design if you can do that.

```html
<!DOCTYPE html>
<html lang="en">
<head>
<meta charset="utf-8">
<title>Quarrow Signal Instruments – Business Card</title>
<link href="https://fonts.googleapis.com/css2?family=Lato:wght@400;700;900&display=swap" rel="stylesheet">
<style>
  :root {
    --backdrop: #2b2b2b;
    --card: #1c1c1d;
    --card-edge: #262627;
    --brand-blue: #119fcc;
    --silver: #b9bbbd;
    --ink-light: #f2f2f2;
    --emboss-line: #3a3a3b;
    --emboss-hi: #5a5a5c;
  }
  * { margin: 0; padding: 0; box-sizing: border-box; }
  html, body {
    width: 1200px; height: 875px; overflow: hidden;
    background: var(--backdrop);
    font-family: "Lato", Arial, sans-serif;
  }
  .sheet {
    width: 1200px; height: 875px;
    display: flex; flex-direction: column;
    align-items: center; justify-content: center; gap: 44px;
  }
  .card {
    width: 580px; height: 330px;
    background: var(--card);
    border: 1px solid var(--card-edge);
    position: relative; overflow: hidden;
    box-shadow: 0 18px 40px rgba(0,0,0,.45);
  }
  /* front */
  .card--front {
    border-radius: 165px 16px 16px 165px;
    display: flex; align-items: center; justify-content: center; gap: 22px;
  }
  .brand-dot {
    width: 64px; height: 64px; border-radius: 50%;
    background: var(--brand-blue);
  }
  .brand-name {
    color: var(--silver);
    font-weight: 700; font-size: 28px;
    letter-spacing: .08em; text-transform: uppercase;
    line-height: 1.15;
  }
  /* back */
  .card--back { border-radius: 16px; }
  .emboss {
    position: absolute; right: -40px; top: 20px;
    width: 300px; height: 300px;
  }
  .holder {
    position: absolute; left: 42px; bottom: 38px;
    color: var(--ink-light);
  }
  .holder__name {
    color: var(--brand-blue);
    font-weight: 900; font-size: 30px; letter-spacing: .03em;
    text-transform: uppercase; line-height: 1;
  }
  .holder__role {
    font-weight: 700; font-size: 17px; margin: 6px 0 20px;
  }
  .contact { list-style: none; }
  .contact li {
    display: flex; align-items: flex-start; gap: 12px;
    font-size: 14px; line-height: 1.45;
  }
  .contact svg { width: 13px; height: 13px; margin-top: 3px; flex: none; fill: var(--brand-blue); }
</style>
</head>
<body>
<main class="sheet">
  <section class="card card--front" aria-label="Card front">
    <span class="brand-dot"></span>
    <span class="brand-name">Quarrow Signal<br>Instruments</span>
  </section>

  <section class="card card--back" aria-label="Card back">
    <svg class="emboss" viewBox="0 0 300 300" aria-hidden="true">
      <circle cx="150" cy="150" r="140" fill="none" stroke="var(--emboss-hi)" stroke-width="2"/>
      <circle cx="150" cy="150" r="137" fill="#19191a" stroke="var(--emboss-line)" stroke-width="2"/>
    </svg>
    <div class="holder">
      <h1 class="holder__name">Owen Harlow</h1>
      <p class="holder__role">Founder &amp; CEO</p>
      <ul class="contact">
        <li><svg viewBox="0 0 12 12"><path d="M6 0a4 4 0 0 0-4 4c0 3 4 8 4 8s4-5 4-8a4 4 0 0 0-4-4zm0 5.5A1.5 1.5 0 1 1 6 2.5a1.5 1.5 0 0 1 0 3z"/></svg><span>1180 Ridgeline Parkway<br>Loveland, CO 80538</span></li>
        <li><svg viewBox="0 0 12 12"><path d="M2.5 0 4.5 3 3.3 4.3a7 7 0 0 0 4.4 4.4L9 7.5l3 2-1.2 2C5 12 0 7 .5 1.2z"/></svg><span>+001 303 555 0142</span></li>
        <li><svg viewBox="0 0 12 12"><path d="M3 0h6v3H3zM0 4h12v6H9v2H3v-2H0zm4 4v3h4V8z"/></svg><span>+001 303 555 0187</span></li>
        <li><svg viewBox="0 0 12 12"><path d="M0 2h12v1L6 7 0 3zm0 2.3 6 4 6-4V10H0z"/></svg><span>marlene@quarrowsignal.com</span></li>
        <li><svg viewBox="0 0 12 12"><path d="M6 0a6 6 0 1 0 0 12A6 6 0 0 0 6 0zm0 1.5c.6.7 1.1 1.9 1.3 3.5H4.7C4.9 3.4 5.4 2.2 6 1.5zM4.7 7h2.6c-.2 1.6-.7 2.8-1.3 3.5-.6-.7-1.1-1.9-1.3-3.5z"/></svg><span>quarrowsignal.com</span></li>
      </ul>
    </div>
  </section>
</main>
</body>
</html>
```